Website Design for The Elder Nook

Please design and code a new website.
Here are the sites I like best:
http://www.voyaglint.com/alternate/
http://www.wheelgiftbay.org
Please make it similar but look at the competitor site (below) for images and wording. This is NOT a car donation site. It's a senior lead placement site like https://www.kinhavenfinder.com. I just like this sites above as a lead generation sites.
Competitor site:
https://www.kinhavenfinder.com (use ideas / verbiage from this site)
Updates
Competitor site:
Coding
Coded - Design and coding required
Number of Pages Required
1 page
Look and feel
Each slider illustrates characteristics of the customer's brand and the style your logo design should communicate.

```html
<!DOCTYPE html>
<html lang="en">
<head>
<meta charset="utf-8">
<title>The Elder Nook – Senior Living Advisors</title>
<link href="https://fonts.googleapis.com/css2?family=Lato:ital,wght@0,400;0,700;1,400&family=Noticia+Text:ital,wght@0,400;1,400;1,700&family=Oswald:wght@400;500&display=swap" rel="stylesheet">
<style>
:root{
  --navy:#0d2a4a;
  --navy-deep:#0a2340;
  --green:#8cc63f;
  --blue:#1552a8;
  --icon-blue:#1d5aa8;
  --text:#333a44;
  --muted:#6b7480;
  --line:#e3e7ec;
  --field:#dfe3e8;
}
*{box-sizing:border-box;margin:0;padding:0}
html,body{width:1200px;height:3278px;overflow:hidden;background:#fff}
body{position:relative;font-family:'Lato',sans-serif;color:var(--text)}
.abs{position:absolute}
.serif{font-family:'Noticia Text',serif}
.accent{color:var(--green);font-style:italic;font-weight:700}

/* header */
.site-header{left:0;top:0;width:1200px;height:92px;background:#fff}
.brand{left:141px;top:22px;display:flex;align-items:center;gap:12px}
.brand-mark{width:34px;height:34px;border-radius:50%;background:var(--green)}
.brand-name{font-family:'Noticia Text',serif;font-size:34px;color:var(--navy)}
.call-box{left:648px;top:22px;display:flex;align-items:center;gap:10px}
.call-small{font-size:10px;color:var(--muted)}
.call-num{font-family:'Oswald',sans-serif;font-size:24px;color:var(--navy);line-height:1}
.badge{left:865px;top:19px;width:92px;height:48px;border-radius:4px;background:var(--navy)}
.lang{left:1025px;top:35px;display:flex;align-items:center;gap:4px}
.lang-dot{width:16px;height:16px;border-radius:50%;background:#c8283a;border:3px solid #2c4b8f}

/* nav */
.main-nav{left:0;top:92px;width:1200px;height:49px;background:var(--navy)}
.nav-list{display:flex;list-style:none;position:absolute;left:141px;top:0;height:49px}
.nav-list li{font-family:'Oswald',sans-serif;font-size:15px;color:#fff;padding:0 17px;line-height:49px;letter-spacing:.2px}
.nav-list li.active{background:var(--green)}

/* hero */
.hero{left:0;top:141px;width:1200px;height:494px;background:linear-gradient(100deg,#5b5552 0%,#8a7a6c 30%,#c9b59d 55%,#9a8b7c 80%,#6c6660 100%)}
.hero-text{left:141px;top:458px;font-family:'Noticia Text',serif;font-size:33px;color:#fff;line-height:42px}
.inquiry{left:695px;top:179px;width:364px;height:409px;background:rgba(20,48,82,.88)}
.inquiry h2{position:absolute;top:30px;width:100%;text-align:center;font-family:'Noticia Text',serif;font-weight:400;font-size:24px;color:#fff}
.field{position:absolute;left:29px;width:305px;height:41px;background:var(--field);border-radius:3px;display:flex}
.field .ico{width:38px;border-right:1px solid #c4cad1;display:flex;justify-content:center;padding-top:13px}
.field span.ph{padding:13px 0 0 18px;font-size:13px;color:#6b7480}
.submit{position:absolute;left:29px;top:336px;width:305px;height:37px;background:var(--blue);border-radius:3px;color:#fff;font-family:'Noticia Text',serif;font-weight:700;font-size:15px;text-align:center;line-height:37px}

/* support */
.support-photo{left:141px;top:737px;width:424px;height:388px;background:linear-gradient(180deg,#9fc7ea 0%,#c4d7e3 45%,#8d8b86 100%)}
.support-title{left:615px;top:734px;font-family:'Noticia Text',serif;font-size:29px;color:var(--navy);line-height:42px}
.support-copy{left:615px;top:824px;width:450px;font-size:13.5px;line-height:24px}
.feature-list{left:615px;top:883px;list-style:none}
.feature-list li{display:flex;align-items:center;gap:14px;height:48.3px;font-size:14px}
.f-ico{width:36px;height:36px;border-radius:50%;background:var(--icon-blue);display:flex;align-items:center;justify-content:center}
.f-ico.green{background:var(--green)}

/* no cost */
.no-cost{left:141px;top:1196px;width:918px;height:176px;border:1px solid var(--line);border-radius:4px;box-shadow:0 8px 22px rgba(140,198,63,.18);text-align:center}
.no-cost h2{margin-top:36px;font-family:'Noticia Text',serif;font-style:italic;font-weight:700;font-size:30px;color:var(--navy)}
.no-cost p{margin-top:8px;font-style:italic;font-size:16px;color:#3d4550}
.no-cost .call{margin-top:6px;font-family:'Oswald',sans-serif;font-weight:500;font-size:34px;color:var(--navy)}
.no-cost .call b{color:var(--green);font-weight:500}

/* advisor */
.advisor{left:0;top:1475px;width:1200px;height:494px;background:linear-gradient(90deg,#1d2f48 0%,#2a3e5a 25%,#1b3150 45%,#13294a 100%)}
.advisor-box{left:424px;top:1531px;width:635px;height:388px;background:#fff;text-align:center}
.advisor-box h2{margin-top:40px;font-family:'Noticia Text',serif;font-style:italic;font-weight:400;font-size:28px;color:var(--navy)}
.advisor-box .lead{margin-top:14px;font-size:14px}
.perks{display:flex;justify-content:space-between;margin:36px 46px 0 40px}
.perk{width:160px;font-size:14px;line-height:19px;color:#3d4550}
.perk svg{display:block;margin:0 auto 14px}
.search{position:absolute;left:43px;top:282px;width:548px;height:45px;border:1px solid var(--line);display:flex}
.search .in{flex:1;text-align:left;padding:14px 18px;font-size:14px;color:#444}
.search .btn{width:245px;margin:2px;background:var(--green);color:#fff;font-family:'Noticia Text',serif;font-weight:700;font-size:15px;line-height:41px}

/* testimonials */
.reviews-title{left:0;top:2066px;width:1200px;text-align:center;font-family:'Noticia Text',serif;font-size:30px;color:var(--navy)}
.review{top:2160px;width:439px;height:204px;border:1px solid var(--line);border-radius:3px}
.avatar{position:absolute;left:25px;top:36px;width:56px;height:56px;border-radius:50%;border:2px solid #d7dbe0;background:#e9edf1}
.r-name{position:absolute;left:98px;top:40px;font-family:'Noticia Text',serif;font-weight:700;font-size:15px;color:var(--navy)}
.stars{position:absolute;left:98px;top:60px;color:#f26b21;font-size:12px;letter-spacing:2px}
.quote{position:absolute;right:18px;top:38px}
.r-text{position:absolute;left:22px;top:106px;width:400px;font-size:12.5px;line-height:23px;color:#2b323c}
.arrow{top:2240px}

/* veterans */
.veterans{left:0;top:2414px;width:1200px;height:318px;background:linear-gradient(180deg,#1f3a64 0%,#2b3f68 50%,#3b3561 100%);text-align:center;color:#fff}
.veterans h2{margin-top:72px;font-family:'Noticia Text',serif;font-style:italic;font-weight:700;font-size:34px}
.veterans p{margin:14px auto 0;width:900px;font-size:16px;line-height:28px}
.vet-btn{display:inline-block;margin-top:22px;width:130px;height:36px;background:var(--green);border-radius:3px;font-family:'Noticia Text',serif;font-weight:700;font-size:14px;line-height:36px}

/* states */
.states-title{left:0;top:2828px;width:1200px;text-align:center;font-family:'Noticia Text',serif;font-size:30px;color:var(--navy)}
.state-col{top:2893px;list-style:none}
.state-col li{font-size:13px;height:25.5px;color:#2b323c}
.state-col li::before{content:'›';color:var(--green);margin-right:8px;font-weight:700}

/* footer */
.footer-nav{left:0;top:3165px;width:1200px;height:77px;background:var(--navy-deep)}
.footer-nav ul{display:flex;list-style:none;justify-content:center;padding-top:27px;gap:0}
.footer-nav li{font-family:'Oswald',sans-serif;font-size:15px;color:#fff;padding:0 17px}
.footer-bar{left:0;top:3242px;width:1200px;height:36px;background:var(--green)}
.copyright{position:absolute;left:143px;top:10px;font-size:12px;color:var(--navy)}
.socials{position:absolute;left:945px;top:6px;display:flex;gap:7px}
.socials span{width:23px;height:23px;border-radius:50%;background:var(--navy)}
</style>
</head>
<body>

<header class="abs site-header">
  <div class="abs brand"><span class="brand-mark"></span><span class="brand-name">The Elder Nook</span></div>
  <div class="abs call-box">
    <svg width="28" height="28" viewBox="0 0 24 24" fill="none" stroke="#1d5aa8" stroke-width="1.6"><path d="M5 3h4l2 5-2.5 1.5a11 11 0 0 0 6 6L16 13l5 2v4a2 2 0 0 1-2 2A17 17 0 0 1 3 5a2 2 0 0 1 2-2z"/></svg>
    <div><div class="call-small">Talk to a local advisor for FREE</div><div class="call-num">(123) 456-7890</div></div>
  </div>
  <div class="abs badge"></div>
  <div class="abs lang"><span class="lang-dot"></span><svg width="10" height="8" viewBox="0 0 10 8"><path d="M1 2l4 4 4-4" stroke="#333" fill="none" stroke-width="1.4"/></svg></div>
</header>

<nav class="abs main-nav">
  <ul class="nav-list">
    <li class="active">ASSISTED LIVING</li><li>MEMORY CARE</li><li>NURSING HOMES</li><li>MORE LIVING OPTIONS ⌄</li><li>PLANNING &amp; ADVICE</li><li>HOW OUR SERVICE WORKS</li>
  </ul>
</nav>

<section class="abs hero" role="img" aria-label="Photo of an older couple embracing and smiling in a kitchen"></section>
<div class="abs hero-text">You know your family.<br>We know <i>Senior Living</i>.</div>
<form class="abs inquiry">
  <h2>Quick <span style="color:var(--green)">Inquiry</span></h2>
  <div class="field" style="top:86px"><div class="ico"><svg width="12" height="12" viewBox="0 0 12 12" fill="#555"><circle cx="6" cy="3.5" r="3"/><path d="M0 12a6 5 0 0 1 12 0z"/></svg></div><span class="ph">Name</span></div>
  <div class="field" style="top:139px"><div class="ico"><svg width="12" height="12" viewBox="0 0 24 24" fill="#555"><path d="M5 2h4l2 6-3 2a12 12 0 0 0 6 6l2-3 6 2v4a3 3 0 0 1-3 3A19 19 0 0 1 2 5a3 3 0 0 1 3-3z"/></svg></div><span class="ph">Phone</span></div>
  <div class="field" style="top:193px"><div class="ico"><svg width="13" height="10" viewBox="0 0 13 10"><rect width="13" height="10" fill="#555"/><path d="M0 0l6.5 5L13 0" stroke="#dfe3e8" fill="none"/></svg></div><span class="ph">Email</span></div>
  <div class="field" style="top:246px;height:69px"><div class="ico"><svg width="14" height="11" viewBox="0 0 14 11" fill="#555"><ellipse cx="5.5" cy="4" rx="5.5" ry="4"/><ellipse cx="9" cy="7" rx="5" ry="3.5"/></svg></div><span class="ph">Message</span></div>
  <div class="submit">Submit Now</div>
</form>

<div class="abs support-photo" role="img" aria-label="Photo of four smiling seniors with bicycles at the beach"></div>
<h2 class="abs support-title">The support you need to make the<br><span class="accent">Right Choice</span></h2>
<p class="abs support-copy">Lorem ipsum dolor sit amet, consectetuer adipiscing elit, sed &nbsp;nonummy nibh euismod tincidunt ut laoreet dolore magna aliquam erat</p>
<ul class="abs feature-list">
  <li><span class="f-ico"><svg width="16" height="16" viewBox="0 0 16 16" fill="none" stroke="#fff"><circle cx="8" cy="4" r="2.5"/><path d="M3 15v-5a5 4 0 0 1 10 0v5"/></svg></span>Dedicated local advisor</li>
  <li><span class="f-ico"><svg width="16" height="16" viewBox="0 0 16 16" fill="none" stroke="#fff"><path d="M2 8l6-6 6 6M4 7v7h8V7"/></svg></span>Hand-picked list of communities to match your needs</li>
  <li><span class="f-ico green"><svg width="16" height="16" viewBox="0 0 16 16" fill="none" stroke="#fff"><circle cx="8" cy="6" r="4"/><path d="M2 14h12"/></svg></span>Full details &amp; pricing</li>
  <li><span class="f-ico"><svg width="16" height="16" viewBox="0 0 16 16" fill="none" stroke="#fff"><rect x="2" y="3" width="12" height="11"/><path d="M2 6h12M5 1v3M11 1v3"/></svg></span>Help scheduling tours</li>
  <li><span class="f-ico"><svg width="18" height="14" viewBox="0 0 18 14" fill="none" stroke="#fff"><rect x="1" y="2" width="10" height="8"/><path d="M11 5h4l2 3v2h-6"/><circle cx="4" cy="11.5" r="1.5"/><circle cx="14" cy="11.5" r="1.5"/></svg></span>Move in support</li>
</ul>

<section class="abs no-cost">
  <h2>There's No Cost To You</h2>
  <p>We work with over 20,000 senior living communities. Our community partners pay us for placement services.</p>
  <div class="call">CALL <b>866-555-0142</b></div>
</section>

<section class="abs advisor" role="img" aria-label="Photo of a smiling advisor in a suit in an office"></section>
<div class="abs advisor-box">
  <h2>Your <span class="accent">Local Advisor</span> Informs. You Decide.</h2>
  <p class="lead">Over 400 senior advisors across the U.S. and Canada are ready to help your family with:</p>
  <div class="perks">
    <div class="perk"><svg width="30" height="44" viewBox="0 0 30 44" fill="none" stroke="#8cc63f" stroke-width="1.6"><path d="M15 42S2 24 2 15a13 13 0 0 1 26 0c0 9-13 27-13 27z"/><circle cx="15" cy="15" r="5"/></svg>Insider's tips for the area near you</div>
    <div class="perk"><svg width="46" height="44" viewBox="0 0 46 44" fill="none" stroke="#8cc63f" stroke-width="1.6"><path d="M23 41L5 23a10 10 0 0 1 18-14 10 10 0 0 1 18 14z"/></svg>Advice tailored to your unique situation</div>
    <div class="perk"><svg width="42" height="44" viewBox="0 0 42 44" fill="none" stroke="#8cc63f" stroke-width="1.6"><circle cx="5" cy="8" r="3"/><circle cx="5" cy="22" r="3"/><circle cx="5" cy="36" r="3"/><path d="M14 8h26M14 22h26M14 36h26"/></svg>Time saving know-how and resources</div>
  </div>
  <div class="search"><div class="in">Enter city or postal code</div><div class="btn">Find An Advisor Near You</div></div>
</div>

<h2 class="abs reviews-title">93% Of Our <span class="accent">Customers Recommend</span> Our Service</h2>
<svg class="abs arrow" style="left:88px" width="22" height="44" viewBox="0 0 22 44"><path d="M20 2L2 22l18 20" stroke="#1d5aa8" fill="none" stroke-width="1.6"/></svg>
<svg class="abs arrow" style="left:1090px" width="22" height="44" viewBox="0 0 22 44"><path d="M2 2l18 20L2 42" stroke="#8cc63f" fill="none" stroke-width="1.6"/></svg>
<article class="abs review" style="left:141px">
  <div class="avatar" role="img" aria-label="Portrait of reviewer"></div>
  <div class="r-name">Marla Quince</div><div class="stars">★★★★★</div>
  <svg class="quote" width="52" height="44" viewBox="0 0 52 44" fill="#e6f1d8"><path d="M0 20a16 16 0 0 1 16-16v8a8 8 0 0 0-8 8h8v22H0zM28 20a16 16 0 0 1 16-16v8a8 8 0 0 0-8 8h8v22H28z"/></svg>
  <p class="r-text">Lorem ipsum dolor sit amet, consectetuer adipiscing elit, sed diam nonummy nibh euismod tincidunt ut laoreet dolore magna aliquam erat volutpat. Ut wisi enim ad minim veniam, quis</p>
</article>
<article class="abs review" style="left:621px">
  <div class="avatar" role="img" aria-label="Portrait of reviewer"></div>
  <div class="r-name">Dorian Hollis</div><div class="stars">★★★★★</div>
  <svg class="quote" width="52" height="44" viewBox="0 0 52 44" fill="#e6f1d8"><path d="M0 20a16 16 0 0 1 16-16v8a8 8 0 0 0-8 8h8v22H0zM28 20a16 16 0 0 1 16-16v8a8 8 0 0 0-8 8h8v22H28z"/></svg>
  <p class="r-text">Lorem ipsum dolor sit amet, consectetuer adipiscing elit, sed diam nonummy nibh euismod tincidunt ut laoreet dolore magna aliquam erat volutpat. Ut wisi enim ad minim veniam, quis</p>
</article>

<section class="abs veterans" role="img" aria-label="Background of a waving national flag in deep blue and red tones">
  <h2>Access Up To <span style="color:var(--green)">$2,000 Per Month</span> In Veteran's Aid</h2>
  <p>We work with Veterans every day. Most veteran families do not know of a key benefit available to them &amp; their families. It's called the Veteran's Aid &amp; Attendance benefit. This benefit can help pay for senior living &amp; home care.</p>
  <span class="vet-btn">Learn More</span>
</section>

<h2 class="abs states-title">Senior Assisted <span class="accent">Living by State</span></h2>
<ul class="abs state-col" style="left:141px"><li>Alabama</li><li>Arizona</li><li>Arkansas</li><li>California</li><li>Colorado</li><li>Connecticut</li><li>Delaware</li></ul>
<ul class="abs state-col" style="left:288px"><li>District of Columbia</li><li>Florida</li><li>Georgia</li><li>Hawaii</li><li>Idaho</li><li>Illinois</li><li>Indiana</li></ul>
<ul class="abs state-col" style="left:478px"><li>Iowa</li><li>Kansas</li><li>Kentucky</li><li>Louisiana</li><li>Maine</li><li>Maryland</li><li>Massachusetts</li></ul>
<ul class="abs state-col" style="left:640px"><li>Michigan</li><li>Minnesota</li><li>Mississippi</li><li>Missouri</li><li>Montana</li><li>Nebraska</li><li>Nevada</li></ul>
<ul class="abs state-col" style="left:780px"><li>New Hampshire</li><li>New Jersey</li><li>New Mexico</li><li>New York</li><li>North Carolina</li><li>North Dakota</li><li>Ohio</li></ul>
<ul class="abs state-col" style="left:949px"><li>Oklahoma</li><li>Oregon</li><li>Pennsylvania</li><li>Rhode Island</li><li>South Carolina</li><li>South Dakota</li><li>Tennessee</li></ul>

<footer>
  <nav class="abs footer-nav">
    <ul><li>ASSISTED LIVING</li><li>MEMORY CARE</li><li>NURSING HOMES</li><li>MORE LIVING OPTIONS ⌄</li><li>PLANNING &amp; ADVICE</li><li>HOW OUR SERVICE WORKS</li></ul>
  </nav>
  <div class="abs footer-bar">
    <p class="copyright">Copyright 2019 The Elder Nook. All Rights Reserved.</p>
    <div class="socials"><span></span><span></span><span></span><span></span></div>
  </div>
</footer>

</body>
</html>
```